FernPath....... a dash of Glow

I need a web design for a new business based in London that will be mobile (offered at homes, parks or a local cafe ect) called FernPath. I offer Life Coaching/Counselling sessions, Personal training, Massage and Sports Massage. Sessions range from an hour to half and hour. My aim is to help people along their journey to help give them gain clarity of where there going, helping them to towards their goals, so that can experience bliss. My website should represent a place people can come to release their stress and worries so that they leave feeling lighter, clearer and happier. I would like my website to reflect someone feeling ALIVE. I would also like a logo design for FernPath with a sentence underneath or near saying A Dash of Glow.

Target Market(s)

middle class people

Industry/Entity Type

Business

Coding

Coded - Design and coding required

Number of Pages Required

4 page

Requirements
Must have
• 1st page About us
• 2nd page Services
• 3rd page Prices
• 4th page contact details
Nice to have
• mixture of cultures in images

```html
<!DOCTYPE html>
<html lang="en">
<head>
<meta charset="utf-8">
<title>FernPath — A Dash of Glow</title>
<link rel="stylesheet" href="https://fonts.googleapis.com/css2?family=Raleway:wght@400;500;600;700&family=Open+Sans:wght@400;600;700&display=swap">
<style>
:root{
  --teal:#3dbaa2;
  --teal-dark:#2fa58e;
  --yellow:#f7e93a;
  --ink:#1d1d1d;
  --muted:#6d6d6d;
  --white:#ffffff;
  --sun-1:#fbe7a6;
  --sun-2:#f6b743;
  --sun-3:#c9803a;
}
*{margin:0;padding:0;box-sizing:border-box}
html,body{width:1200px;height:2521px;overflow:hidden}
body{position:relative;background:var(--white);font-family:"Open Sans",sans-serif;color:var(--ink)}
.abs{position:absolute}

/* header */
.header{position:absolute;left:0;top:0;width:1200px;height:143px;background:var(--white)}
.topbar{position:absolute;left:0;top:0}
.topbar-item{position:absolute;top:13px;color:var(--white);font-size:16px;display:flex;align-items:center;gap:10px;white-space:nowrap}
.social-dot{width:12px;height:12px;border-radius:50%;background:var(--white);display:inline-block}
.brand{position:absolute;left:122px;top:22px;color:var(--teal);font-family:"Raleway",sans-serif;font-weight:600}
.brand-name{font-size:38px;letter-spacing:1px;line-height:1}
.brand-tag{font-size:13px;margin-top:8px}
.nav{position:absolute;top:88px;left:0;width:1200px;font-family:"Raleway",sans-serif;font-size:13px;font-weight:500;color:var(--ink)}
.nav a{position:absolute;color:inherit;text-decoration:none;transform:translateX(-50%);white-space:nowrap}

/* hero */
.hero{position:absolute;left:0;top:143px;width:1200px;height:591px;
  background:radial-gradient(circle at 66% 72%,#fffbe8 0,var(--sun-1) 12%,var(--sun-2) 38%,var(--sun-3) 100%)}
.hero-title{position:absolute;left:148px;top:238px;font-family:"Raleway",sans-serif;color:#2b2b2b}
.hero-title .small{font-size:33px;font-weight:500;letter-spacing:1px}
.hero-title .big{font-size:76px;font-weight:400;color:var(--teal);line-height:1;letter-spacing:2px}
.dots{position:absolute;top:552px;left:525px;display:flex;gap:19px}
.dot{width:13px;height:13px;border:2px solid #3a3a3a;border-radius:50%}
.dot.active{background:var(--teal);border-color:var(--teal)}

/* sections */
.section-title{position:absolute;left:0;width:1200px;text-align:center;font-family:"Raleway",sans-serif;font-weight:700;font-size:29px;letter-spacing:1px}
.section-title span{color:var(--teal)}
.services-sub{position:absolute;top:832px;left:0;width:1200px;text-align:center;font-size:13px;color:var(--muted)}
.service{position:absolute;top:908px;width:360px;text-align:center}
.service-photo{width:200px;height:200px;border-radius:50%;border:4px solid var(--yellow);margin:0 auto}
.service-label{margin-top:35px;font-family:"Raleway",sans-serif;font-size:15px;font-weight:500;letter-spacing:.5px}

.about{position:absolute;left:0;top:1236px;width:1200px;height:488px;background:var(--teal)}
.about-photo{position:absolute;left:79px;top:81px;width:517px;height:319px;background:linear-gradient(135deg,#cfc6bd,#9ea7ae 60%,#d9d3cc);box-shadow:0 6px 14px rgba(0,0,0,.2)}
.about-copy{position:absolute;left:643px;top:88px;width:476px;color:var(--white);font-size:13px;line-height:24px;text-align:justify}
.about-copy h2{font-family:"Raleway",sans-serif;font-size:33px;font-weight:700;letter-spacing:1px;margin-bottom:18px;line-height:1.2}
.about-copy p{margin-bottom:24px}
.btn{position:absolute;left:642px;top:352px;width:165px;height:44px;border-radius:22px;background:var(--yellow);color:var(--ink);font-size:14px;font-weight:600;display:flex;align-items:center;justify-content:center;gap:8px}

.blog{position:absolute;left:0;top:1724px;width:1200px;height:560px;background:linear-gradient(180deg,#fffaf0,#fbf3e6 55%,#f6f3f2)}
.post{position:absolute;top:128px;width:323px}
.post-photo{width:323px;height:225px}
.post-date{position:absolute;left:66px;top:200px;width:190px;height:45px;border-radius:22px 22px 0 0;background:var(--yellow);font-family:"Raleway",sans-serif;font-size:14px;display:flex;align-items:center;justify-content:center;gap:6px;white-space:nowrap}
.post-date b{font-size:21px}
.post h3{margin-top:35px;font-family:"Raleway",sans-serif;font-size:15px;font-weight:700;letter-spacing:.3px;white-space:nowrap}
.post p{margin-top:18px;font-size:13px;line-height:24px;color:var(--muted)}

.footer{position:absolute;left:0;top:2276px;width:1200px;height:245px;background:var(--teal)}
.footer-card{position:absolute;left:79px;top:2243px;width:1040px;height:223px;background:var(--yellow);box-shadow:0 4px 10px rgba(0,0,0,.15)}
.footer-head{font-family:"Raleway",sans-serif;font-weight:700;font-size:15px;color:var(--teal);display:flex;align-items:center;gap:8px;white-space:nowrap}
.timing{position:absolute;left:42px;top:52px}
.hours{margin-top:14px;display:grid;grid-template-columns:76px 180px;row-gap:1px;align-items:center}
.hours dt{font-size:11px;text-align:right;padding-right:12px;font-weight:600;white-space:nowrap}
.hours dd{font-size:17px;white-space:nowrap;line-height:24px}
.footer-brand{position:absolute;left:0;width:1040px;top:52px;text-align:center;font-family:"Raleway",sans-serif;font-weight:600;color:var(--teal);font-size:34px;letter-spacing:1px}
.footer-social{position:absolute;top:148px;left:456px;display:flex;gap:14px}
.footer-social span{width:38px;height:38px;border:2px solid var(--ink);border-radius:50%;display:flex;align-items:center;justify-content:center}
.footer-social span::after{content:"";width:12px;height:12px;border-radius:50%;background:var(--ink)}
.contact{position:absolute;left:740px;top:52px}
.contact-row{display:flex;align-items:baseline;gap:12px;margin-top:16px;white-space:nowrap}
.contact-row small{width:64px;text-align:right;font-size:11px;font-weight:600}
.contact-row strong{font-size:21px}
.contact-row strong.mail{font-size:17px}
.copyright{position:absolute;top:2482px;left:0;width:1200px;text-align:center;color:var(--white);font-size:13px}
.copyright b{color:var(--yellow)}
</style>
</head>
<body>

<header class="header">
  <svg class="topbar" width="1200" height="52" viewBox="0 0 1200 52" aria-hidden="true">
    <path d="M328 0 H1200 V50 H420 Q360 40 328 0 Z" fill="var(--teal)"/>
    <line x1="630" y1="8" x2="630" y2="42" stroke="#ffffff" stroke-opacity=".4"/>
    <line x1="880" y1="8" x2="880" y2="42" stroke="#ffffff" stroke-opacity=".4"/>
  </svg>
  <div class="topbar-item" style="left:490px"><span class="social-dot"></span><span class="social-dot"></span><span class="social-dot"></span></div>
  <div class="topbar-item" style="left:656px;font-size:15px">
    <svg width="16" height="12" viewBox="0 0 16 12"><rect width="16" height="12" rx="1" fill="#fff"/><path d="M0 1 L8 7 L16 1" stroke="var(--teal)" fill="none" stroke-width="1.5"/></svg>
    hello@fernpath.example
  </div>
  <div class="topbar-item" style="left:936px;font-size:19px">
    <svg width="16" height="16" viewBox="0 0 24 24"><path fill="#fff" d="M6.6 10.8a15 15 0 0 0 6.6 6.6l2.2-2.2a1 1 0 0 1 1-.25 11.4 11.4 0 0 0 3.6.6 1 1 0 0 1 1 1V20a1 1 0 0 1-1 1A17 17 0 0 1 3 4a1 1 0 0 1 1-1h3.5a1 1 0 0 1 1 1c0 1.25.2 2.45.6 3.6a1 1 0 0 1-.25 1z"/></svg>
    (800) 555-0142
  </div>
  <div class="brand">
    <div class="brand-name">FERNPATH</div>
    <div class="brand-tag">A Dash of Glow</div>
  </div>
  <nav class="nav">
    <a style="left:397px">HOME</a><a style="left:497px">ABOUT</a><a style="left:607px">SERVICES</a><a style="left:712px">CLASSES</a><a style="left:858px">TESTIMONIALS</a><a style="left:980px">BLOG</a><a style="left:1086px">CONTACT</a>
  </nav>
</header>

<section class="hero" role="img" aria-label="Woman with arms raised against a golden sunset sky over the sea">
  <h1 class="hero-title"><div class="small">A DASH OF</div><div class="big">GLOW</div></h1>
  <div class="dots"><span class="dot"></span><span class="dot"></span><span class="dot active"></span><span class="dot"></span><span class="dot"></span></div>
</section>

<h2 class="section-title" style="top:780px">OUR <span>SERVICES</span></h2>
<p class="services-sub">A wonderful sereny has taken possession of soul, like these sweet mornings of idma aute rure dolor in reprehendet</p>
<div class="service" style="left:67px">
  <div class="service-photo" role="img" aria-label="Counselling session between two people" style="background:linear-gradient(135deg,#e9e4e2,#b89aa6 55%,#6d4c5a)"></div>
  <div class="service-label">COUNSELLING SESSIONS</div>
</div>
<div class="service" style="left:417px">
  <div class="service-photo" role="img" aria-label="Group stretching in a personal training class" style="background:linear-gradient(135deg,#f2f2f2,#c9b7d4 50%,#8fa9b5)"></div>
  <div class="service-label">PERSONAL TRAINING</div>
</div>
<div class="service" style="left:763px">
  <div class="service-photo" role="img" aria-label="Relaxed client resting during a massage" style="background:linear-gradient(135deg,#a9c26a,#d8b79a 55%,#8a6a55)"></div>
  <div class="service-label">MASSAGE AND SPORTS MASSAGE</div>
</div>

<section class="about">
  <div class="about-photo" role="img" aria-label="Smiling group with exercise balls in a fitness studio"></div>
  <div class="about-copy">
    <h2>FERNPATH</h2>
    <p>Lorem ipsum dolor sit amet, consectetur adipiscing elit. Praesent lacus tellus, imperdiet at enim quis</p>
    <p>Fermentum iaculis arcu. Pellentesque euismod ultrices sem non efficitur. Maecenas sit amet nisl a lorem convallis blandit ac vitae ligula. Proin id est tincidunt, efficitur ante ut, rutrum mauris. In lacinia enim nec velit feugiat varius. Ut dui dolor, dictum tempus consectetur.</p>
  </div>
  <div class="btn">Read More
    <svg width="13" height="13" viewBox="0 0 14 14"><circle cx="7" cy="7" r="7" fill="var(--ink)"/><path d="M5.5 4 L8.5 7 L5.5 10" stroke="var(--yellow)" stroke-width="1.8" fill="none"/></svg>
  </div>
</section>

<section class="blog">
  <h2 class="section-title" style="top:55px;font-size:25px">RECENT FROM <span>BLOG</span></h2>
  <article class="post" style="left:79px">
    <div class="post-photo" role="img" aria-label="Woman smiling over an exercise ball in a gym class" style="background:linear-gradient(135deg,#4a7fc4,#e8d2b8 50%,#2d5fae)"></div>
    <div class="post-date"><b>07</b> OCTOBER 2015</div>
    <h3>PREGNANT YOGA EXERCISES IN 30MIN</h3>
    <p>A wonderful sereny has taken possession of my entire soul, like these sweet mornings of spring.</p>
  </article>
  <article class="post" style="left:438px">
    <div class="post-photo" role="img" aria-label="Group doing side stretches in a bright studio" style="background:linear-gradient(135deg,#f0f0f0,#c9b7d4 50%,#9bb7ba)"></div>
    <div class="post-date"><b>29</b> AUGUST 2015</div>
    <h3>PREGNANT YOGA EXERCISES IN 30MIN</h3>
    <p>A wonderful sereny has taken possession of my entire soul, like these sweet mornings of spring.</p>
  </article>
  <article class="post" style="left:797px">
    <div class="post-photo" role="img" aria-label="Two women stretching beside a blue exercise ball" style="background:linear-gradient(135deg,#e5ddd6,#c7b6a8 50%,#4f7fc2)"></div>
    <div class="post-date"><b>15</b> MARCH 2015</div>
    <h3>PREGNANT YOGA EXERCISES IN 30MIN</h3>
    <p>A wonderful sereny has taken possession of my entire soul, like these sweet mornings of spring.</p>
  </article>
</section>

<footer class="footer"></footer>
<svg class="abs" style="left:62px;top:2243px" width="1076" height="34" viewBox="0 0 1076 34" aria-hidden="true">
  <path d="M0 34 L17 0 V34 Z" fill="var(--teal-dark)"/><path d="M1076 34 L1059 0 V34 Z" fill="var(--teal-dark)"/>
</svg>
<div class="footer-card">
  <div class="timing">
    <div class="footer-head">
      <svg width="15" height="15" viewBox="0 0 16 16"><circle cx="8" cy="8" r="7" fill="none" stroke="var(--teal)" stroke-width="2"/><path d="M8 4 V8 H11" stroke="var(--teal)" stroke-width="2" fill="none"/></svg>TIMING</div>
    <dl class="hours">
      <dt>MON-FRI :</dt><dd>6:00am - 11:00pm</dd>
      <dt>SAT :</dt><dd>7:00am - 10:00pm</dd>
      <dt>SUN :</dt><dd>Closed</dd>
    </dl>
  </div>
  <div class="footer-brand">FERNPATH</div>
  <div class="footer-social" aria-label="Social links"><span></span><span></span><span></span></div>
  <div class="contact">
    <div class="footer-head">
      <svg width="15" height="15" viewBox="0 0 24 24"><path fill="var(--teal)" d="M6.6 10.8a15 15 0 0 0 6.6 6.6l2.2-2.2a1 1 0 0 1 1-.25 11.4 11.4 0 0 0 3.6.6 1 1 0 0 1 1 1V20a1 1 0 0 1-1 1A17 17 0 0 1 3 4a1 1 0 0 1 1-1h3.5a1 1 0 0 1 1 1c0 1.25.2 2.45.6 3.6a1 1 0 0 1-.25 1z"/></svg>JOIN US / CONTACT US</div>
    <div class="contact-row"><small>CALL US :</small><strong>(800) 555-0187</strong></div>
    <div class="contact-row" style="margin-top:8px"><small>EMAIL US :</small><strong class="mail">hello@fernpath.example</strong></div>
  </div>
</div>
<p class="copyright">Copyright © <b>FERNPATH</b>. &nbsp;|&nbsp; All Rights Reserved</p>

</body>
</html>
```